Silver Bloom Marisol's Cleaning Service Business Cards Project

A business card with all contact details with logo design on there (already have a logo) eye catching Logo and contact info on one side, full logo on the back, must target upper class residential and corporate companies, fitness companies, still keep it on the feminine side of things , must look elegant

Target Market(s)

Upper class homes and corporate companies

Industry/Entity Type

Cleaning Service

Contact Information for Business Card

Name: Marisol Quenby
Position: Director
ABN: 31647209853
Email: marisolssilvercleaning@tidymail.example
Number: 0417906354

Font styles to use
Decorative

Colors

Designer to choose colors to be used in the design.

Requirements
Must have
• Available Sydney Wide, contact info and logo on one side, full logo on the back
Nice to have
• Professional appearance
Should not have
• Cheap advert looking stuff

```html
<!DOCTYPE html>
<html lang="en">
<head>
<meta charset="utf-8">
<title>Silver Bloom – Business Cards</title>
<link href="https://fonts.googleapis.com/css2?family=Lora:wght@500&family=Lato:wght@400&display=swap" rel="stylesheet">
<style>
  :root {
    --backdrop: #2b2b2c;
    --card: #1d1e20;
    --teal: #40e0d0;
    --white: #f2f2f2;
    --pattern-a: #232427;
    --pattern-b: #1d1e20;
  }
  * { box-sizing: border-box; margin: 0; padding: 0; }
  html, body { width: 1200px; height: 1108px; overflow: hidden; background: var(--backdrop); }
  .canvas { position: relative; width: 1200px; height: 1108px; }
  .card {
    position: absolute; top: 194px; width: 440px; height: 720px;
    background: var(--card); border-radius: 22px;
    box-shadow: 0 18px 40px rgba(0,0,0,.45);
    display: flex; flex-direction: column; align-items: center;
  }
  .card--front { left: 110px; }
  .card--back { left: 650px; overflow: hidden; }

  .brand { display: flex; flex-direction: column; align-items: center; text-align: center; }
  .brand__mark { width: 22px; height: 22px; border: 2px solid var(--teal); border-radius: 50%; margin-bottom: 14px; }
  .brand__name {
    font-family: "Lora", serif; font-weight: 500; color: var(--teal);
    font-size: 40px; letter-spacing: 1px; text-transform: uppercase; line-height: 1;
  }
  .brand__tagline {
    font-family: "Lato", sans-serif; font-weight: 400; color: var(--teal);
    font-size: 13px; letter-spacing: 4.5px; text-transform: uppercase; margin-top: 10px;
  }
  .card--front .brand { margin-top: 150px; }

  .contact { margin-top: 96px; text-align: center; font-family: "Lato", sans-serif; color: var(--white); }
  .contact__name {
    font-family: "Lora", serif; font-weight: 500; color: var(--teal);
    font-size: 29px; text-transform: uppercase; letter-spacing: .5px;
  }
  .contact__role { font-size: 19px; margin-top: 4px; }
  .contact__line { font-size: 19px; margin-top: 8px; }
  .contact__label { color: var(--teal); }

  .pattern-field {
    position: absolute; inset: 0;
    background: repeating-linear-gradient(45deg, var(--pattern-a) 0 40px, var(--pattern-b) 40px 80px);
    opacity: .8;
  }
  .card--back .brand { position: absolute; bottom: 110px; left: 0; right: 0; }
</style>
</head>
<body>
<main class="canvas">
  <section class="card card--front" aria-label="Business card front">
    <div class="brand">
      <span class="brand__mark"></span>
      <p class="brand__name">Silver Bloom</p>
      <p class="brand__tagline">Marisol's Cleaning Service</p>
    </div>
    <div class="contact">
      <p class="contact__name">Marisol Quenby</p>
      <p class="contact__role">Director</p>
      <p class="contact__line"><span class="contact__label">ABN:</span> 31647209853</p>
      <p class="contact__line">0417906354</p>
      <p class="contact__line">marisolssilvercleaning@tidymail.example</p>
    </div>
  </section>

  <section class="card card--back" aria-label="Business card back">
    <div class="pattern-field" role="img" aria-label="Faint repeating brand pattern across the card back"></div>
    <div class="brand">
      <span class="brand__mark"></span>
      <p class="brand__name">Silver Bloom</p>
      <p class="brand__tagline">Marisol's Cleaning Service</p>
    </div>
  </section>
</main>
</body>
</html>
```